San Francisco Leading Consulting firm - 47Vora Web Design Project

•Create a Web Design
•Uncoded webpage layout design
•2 Pages Design - Homepage + Interior Page

Task Description
Hello, we're looking for a re-design our current website www.47vora-example.com

we have a sample mockup design @

http://47vora.pubtrellis-example.org/

This shows the layout that we like and also a sample of 6 pictures that would change based on where you mouse over..

6 pictures HOME design needs to be included.

SMART
THOUGHTFUL
FLEXIBLE
CREATIVE SERVICES
TECHNICAL SERVICES
PARTNERS

sites we like:

http://www.melvanadvisory-example.com/Home.cfm?id=Home
http://www.plinthworks-example.com/index.html

Our company can be best described as: 100+ employees, cutting-edge, depandable, innovative, strong, smart.

Our Primary focus is: IT Consulting Services and Creative Design services

47Vora LLC is a consulting firm providing creative design, business and technology solutions to both private and public interests.

Established in 1996, 47Vora is a San Francisco based company providing specialists for a range of business needs including:

Creative Design Services
•Print
•Logo Design
•Website Design
•Illustration

and

Business and Technology solutions

•Application Software and Web Development
•Business Process Re-Design (BPR)
•Business/Systems Analysis and Requirement Documentation
•Mentoring and Training
•Network/Hardware Installation Services
•System Design and Architecture
•Vendor Management
•Docuvault Architecture and Implementation

our sample mockup site:

Reason: Due to holiday season, we're not available to work with designers and finilize our design.  

Thank you very much for submitting your design.

We appreciate your time and creativity.   Since, our office is currently closed for holidays, we will be reviewing it in details next week and will make our decision as soon as possible.

It would be great if you could submit any of your changes by Wed next week, so it would be part of our reviews. 

Please see updated wireframe under attachments:  we have some minor updates to our wireframe that we would like you to update your designs, if possible.  

We also encorouge you not to use our standard wireframe and come up with more unique designs.   Everything would be considered when we review your design.

 

Target Market(s)

Creative services and professional services clients, including government agencies

Industry/Entity Type

Business

Requirements
Must have
• Clean, professional look, easy navigation

```html
<!DOCTYPE html>
<html lang="en">
<head>
<meta charset="utf-8">
<title>47Vora LLC — Technology Solutions</title>
<link rel="stylesheet" href="https://fonts.googleapis.com/css2?family=Arimo:ital,wght@0,400;0,700;1,400&family=Carlito:ital,wght@0,400;0,700;1,400&display=swap">
<style>
:root{
  --header-bg:#eef6fa;
  --nav-bg:#dcebf4;
  --ink:#3a3a3a;
  --ink-soft:#5b5b5b;
  --muted:#8a8a8a;
  --brand-blue:#1a86c8;
  --link:#1a72b8;
  --cyan:#34dbef;
  --accent:#f0a020;
  --dot-active:#1fa3e6;
  --icon-creative:#2a8cc9;
  --icon-technical:#9a3a48;
  --icon-partners:#8fb03a;
  --card-line:#e2e4e6;
  --divider:#dedede;
  --quote:#a9d6ee;
}
*{box-sizing:border-box;margin:0;padding:0}
html,body{width:1159px;height:1200px;overflow:hidden}
body{position:relative;font-family:"Carlito",Arial,sans-serif;color:var(--ink);
  background:linear-gradient(180deg,#fff 0,#fff 300px,#e6e8ea 300px,#eceef0 620px,#f7f8f9 820px,#fafbfb 1200px)}
.abs{position:absolute}

.site-header{left:0;top:0;width:1159px;height:100px;background:var(--header-bg)}
.brand{left:147px;top:34px;display:flex;align-items:center;gap:10px}
.brand-dot{width:30px;height:30px;border-radius:50%;background:var(--brand-blue)}
.brand-name{font-family:"Carlito",sans-serif;font-size:30px;letter-spacing:1px;color:#444}
.tagline{left:333px;top:50px;font-size:14px;color:#444}
.contact{left:923px;top:16px;font-size:13px;color:var(--ink-soft);line-height:1.1}
.contact .big{font-size:18px;color:var(--link);margin:3px 0 9px}
.contact .mail{font-size:13px;color:var(--link);margin-top:3px}

.main-nav{left:0;top:100px;width:1159px;height:36px;background:var(--nav-bg)}
.nav-item{top:13px;font-family:"Arimo",sans-serif;font-weight:700;font-size:11px;letter-spacing:.6px;color:#333}
.nav-item .chev{color:var(--accent);margin-left:12px;font-weight:700}
.search{left:872px;top:108px;width:149px;height:21px;background:#fff;border:1px solid #d4dde3;border-radius:2px;
  font-family:"Arimo",sans-serif;font-style:italic;font-size:8px;color:#aaa;padding:5px 7px}
.search svg{position:absolute;right:4px;top:3px}

.welcome-title{left:152px;top:168px;font-weight:400;font-size:38px;color:var(--cyan);line-height:1}
.intro{left:151px;font-size:13px;color:#333;white-space:nowrap}

.slider{left:140px;top:300px;width:878px;height:311px;overflow:hidden}
.slider-photo{position:absolute;left:136px;top:0;width:742px;height:311px;
  background:linear-gradient(100deg,#b8ac98 0%,#e9e3d6 30%,#d2b79a 55%,#9d8a76 75%,#d6d3cd 100%)}
.slider-side{position:absolute;left:0;top:0;width:136px;height:311px;
  background:linear-gradient(180deg,#c48a72 0%,#a7876a 55%,#8a8a5a 100%)}
.slider-arrow{position:absolute;top:140px}
.slide-title{position:absolute;left:56px;top:200px;font-size:48px;color:#fff;line-height:1}
.slide-sub{position:absolute;left:56px;top:254px;font-size:23px;color:#fff}
.dots{position:absolute;left:772px;top:287px;display:flex;gap:6px}
.dots span{width:9px;height:9px;border-radius:50%;background:#fff}
.dots span.on{background:var(--dot-active)}

.service-card{top:648px;width:256px;height:147px;background:linear-gradient(180deg,#fff,#f6f7f8);
  border:1px solid var(--card-line);border-radius:6px;box-shadow:0 2px 4px rgba(0,0,0,.06)}
.service-card .reflect{position:absolute;left:0;top:150px;width:256px;height:50px;border-radius:6px;
  background:linear-gradient(180deg,rgba(255,255,255,.6),rgba(255,255,255,0))}
.card-icon{position:absolute;width:40px;height:40px;border-radius:6px;opacity:.85}
.card-icon.creative{background:var(--icon-creative)}
.card-icon.technical{background:var(--icon-technical)}
.card-icon.partners{background:var(--icon-partners)}
.card-title{position:absolute;font-size:18px;color:#333;line-height:1.15}
.card-title small{display:block;font-size:18px;color:#777}
.more{position:absolute;right:18px;bottom:14px;font-size:12px;color:#444}
.more b{color:var(--accent);margin-left:4px}

.clients{left:144px;top:865px;width:584px;height:86px;background:#fff;border:1px solid #d9dbdd;border-radius:8px}
.clients span{position:absolute;left:15px;top:31px;font-size:17px;color:#555}
.clients svg{position:absolute;right:8px;top:33px}

.testimonials{left:760px;top:862px;width:236px}
.testimonials h3{font-weight:400;font-size:17px;color:#555}
.quote-open{position:absolute;left:0;top:24px;font-family:Georgia,serif;font-size:30px;color:var(--quote);line-height:1}
.quote-text{margin-top:17px;font-style:italic;font-size:11.5px;line-height:1.25;color:#666}
.quote-by{margin-top:4px;text-align:right;font-size:10px;color:#777}
.quote-close{position:absolute;right:0;top:88px;font-family:Georgia,serif;font-size:30px;color:var(--quote);line-height:1}

.list-head{top:990px;font-family:"Arimo",sans-serif;font-weight:700;font-size:12.5px;color:#444}
.svc-list{list-style:none;font-family:"Arimo",sans-serif;font-size:10px;color:var(--link);line-height:1.3}
.svc-list li{position:absolute;left:0;white-space:nowrap}
.svc-list li::before{content:"• ";}
.divider{left:412px;top:977px;width:1px;height:163px;background:var(--divider)}

.footer-band{left:96px;top:1152px;width:917px;height:6px;background:linear-gradient(180deg,rgba(0,0,0,.05),rgba(0,0,0,0))}
.copyright{left:0;top:1172px;width:1148px;text-align:center;font-family:"Arimo",sans-serif;font-size:10.5px;color:#222}
</style>
</head>
<body>

<header class="site-header abs">
  <div class="brand abs"><span class="brand-dot"></span><span class="brand-name">47VORA</span></div>
  <p class="tagline abs">Thechnology Solutions for the 21st Century</p>
  <div class="contact abs">
    <div>Call us at</div>
    <div class="big">800.555.0147</div>
    <div>Email us at</div>
    <div class="mail">info@47vora-example.com</div>
  </div>
</header>

<nav class="main-nav abs">
  <span class="nav-item abs" style="left:151px">COMPANY<span class="chev">›</span></span>
  <span class="nav-item abs" style="left:248px">CREATIVE SERVICES<span class="chev">›</span></span>
  <span class="nav-item abs" style="left:407px">TECHNICAL SERVICES<span class="chev">›</span></span>
  <span class="nav-item abs" style="left:584px">PARTNERS<span class="chev">›</span></span>
  <span class="nav-item abs" style="left:695px">CONTACT US</span>
</nav>
<div class="search abs">SEARCH
  <svg width="14" height="14" viewBox="0 0 14 14"><circle cx="8" cy="6" r="4" fill="none" stroke="#f0a020" stroke-width="1.6"/><line x1="5" y1="9" x2="2" y2="12" stroke="#f0a020" stroke-width="1.8"/></svg>
</div>

<h1 class="welcome-title abs">welcome</h1>
<p class="intro abs" style="top:226px">47Vora LLC is a consulting firm providing creative design, business and technology solutions to both private and public interests.</p>
<p class="intro abs" style="top:257px">Our experts possess broad industry knowledge which can help with technical and businessprocess challenges, delivering solutions that are creative and cost effective.</p>

<section class="slider abs">
  <div class="slider-side"></div>
  <div class="slider-photo" role="img" aria-label="Photo of two business people shaking hands"></div>
  <svg class="slider-arrow" style="left:12px" width="20" height="36" viewBox="0 0 20 36"><polyline points="16,2 3,18 16,34" fill="none" stroke="#fff" stroke-width="2"/></svg>
  <svg class="slider-arrow" style="right:10px" width="20" height="36" viewBox="0 0 20 36"><polyline points="4,2 17,18 4,34" fill="none" stroke="#fff" stroke-width="2"/></svg>
  <div class="slide-title">partners</div>
  <div class="slide-sub">partner with 47VORA award winning team</div>
  <div class="dots"><span></span><span></span><span></span><span></span><span></span><span class="on"></span></div>
</section>

<article class="service-card abs" style="left:145px">
  <div class="card-icon creative" style="left:22px;top:42px" role="img" aria-label="Creative services icon"></div>
  <div class="card-title" style="left:77px;top:46px">Creative<small>Services</small></div>
  <div class="more">Lean More<b>›</b></div>
  <div class="reflect"></div>
</article>

<article class="service-card abs" style="left:449px">
  <div class="card-icon technical" style="left:20px;top:42px" role="img" aria-label="Business and technical services icon"></div>
  <div class="card-title" style="left:75px;top:44px">Business &amp; Technical<small>Services</small></div>
  <div class="more">Lean More<b>›</b></div>
  <div class="reflect"></div>
</article>

<article class="service-card abs" style="left:753px">
  <div class="card-icon partners" style="left:24px;top:46px" role="img" aria-label="Partners icon"></div>
  <div class="card-title" style="left:90px;top:63px">Partners</div>
  <div class="more">Lean More<b>›</b></div>
  <div class="reflect"></div>
</article>

<div class="clients abs"><span>Our Clinets</span>
  <svg width="12" height="18" viewBox="0 0 12 18"><polyline points="3,2 10,9 3,16" fill="none" stroke="#777" stroke-width="2"/></svg>
</div>

<aside class="testimonials abs">
  <h3>Testimonials</h3>
  <span class="quote-open">“</span>
  <p class="quote-text">Lorem ipsum dolor sit amet, consectetuer adiping elit, sed diam nonummy nibh euismod.</p>
  <p class="quote-by">Dana Morrell, CEO of Company</p>
  <span class="quote-close">”</span>
</aside>

<h4 class="list-head abs" style="left:147px">Creative Design Services</h4>
<ul class="svc-list abs" style="left:160px;top:1023px">
  <li style="top:0">Print</li>
  <li style="top:25px">Logo Design</li>
  <li style="top:50px">Website Design</li>
  <li style="top:76px">Illustration</li>
</ul>

<div class="divider abs"></div>

<h4 class="list-head abs" style="left:459px">Business and Technical solutions</h4>
<ul class="svc-list abs" style="left:473px;top:1023px">
  <li style="top:0">Application Software and Web Development</li>
  <li style="top:25px">Business Process Re-Design (BPR)</li>
  <li style="top:50px">Business/Systems Analysis and Requirement<br>&nbsp;&nbsp;Documentation</li>
  <li style="top:89px">Mentoring and Training</li>
</ul>
<ul class="svc-list abs" style="left:732px;top:1023px">
  <li style="top:0">Network/Hardware Installation Services</li>
  <li style="top:25px">System Design and Architecture</li>
  <li style="top:50px">Vendor Management</li>
  <li style="top:76px">Docuvault Architecture and Implementation</li>
</ul>

<div class="footer-band abs"></div>
<footer class="copyright abs">Copyright 2010, 47Vora, LLC All rights reserved.</footer>

</body>
</html>
```